Home Staging Company needs business card design

We're a home staging company called Brightly Settled Home Staging. We would like a business card design that includes aqua and gray. Our current logo of house within chair is fine but I find we almost always use the logo in one color. I'll upload images of front and back of our current card and our logo. Note that we have dropped "Solutions" from our company name and don't want to include it on the card.

Target Market(s)

Realtors and homeowners - people interested in selling their homes

Contact Information for Business Card

Marisol Thistlewood
Brightly Settled Home Staging
757-555-0193
www.brightlysettled.com
marisol@brightlysettled.com

Font styles to use
Serif
Script

Requirements
Must have
• My logo and contact details
• UPDATE***
• I forgot to say that the company name should be included on the front of the card somehow.

```html
<!DOCTYPE html>
<html lang="en">
<head>
<meta charset="utf-8">
<title>Brightly Settled Home Staging – Business Card</title>
<link rel="stylesheet" href="https://fonts.googleapis.com/css2?family=Raleway:wght@400;500;600&display=swap">
<style>
  :root {
    --backdrop: #3b3b3d;
    --card-black: #1e1e20;
    --emboss: #39393c;
    --aqua: #56b9c4;
    --stripe-dark: #2f3236;
    --stripe-mid: #4a4f55;
    --white: #ffffff;
    --muted: #c9c9c9;
  }
  * { box-sizing: border-box; margin: 0; padding: 0; }
  html, body {
    width: 799px; height: 1200px; overflow: hidden;
    background: var(--backdrop);
    font-family: "Raleway", Arial, sans-serif;
  }
  .sheet {
    position: relative; width: 799px; height: 1200px;
    display: flex; flex-direction: column; align-items: center;
    justify-content: space-around; padding: 60px 0;
  }
  .card {
    position: relative; width: 640px; height: 366px;
    background: var(--card-black);
    border-radius: 3px;
    box-shadow: 0 14px 30px rgba(0,0,0,.45);
    overflow: hidden;
  }
  /* front */
  .card-front { display: flex; align-items: center; justify-content: center; }
  .front-brand {
    display: flex; align-items: center; gap: 16px;
    color: var(--emboss); font-weight: 600; font-size: 30px; letter-spacing: .5px;
  }
  .front-brand .dot {
    width: 34px; height: 34px; border-radius: 50%; background: var(--emboss);
  }
  /* back */
  .wave { position: absolute; inset: 0; width: 100%; height: 100%; }
  .brand {
    position: absolute; left: 40px; top: 40px;
    display: flex; align-items: center; gap: 12px;
    color: var(--white); font-weight: 600; font-size: 24px; letter-spacing: .3px;
  }
  .brand .dot { width: 26px; height: 26px; border-radius: 50%; background: var(--aqua); }
  .person { position: absolute; left: 40px; top: 100px; }
  .person-name { font-size: 22px; font-weight: 500; color: var(--white); }
  .person-name .surname { color: var(--aqua); }
  .person-title { font-size: 11px; color: var(--muted); margin-top: 4px; }
  .contacts {
    position: absolute; right: 34px; bottom: 34px;
    list-style: none; text-align: right;
    color: var(--white); font-size: 15px; line-height: 1.55;
  }
  .contacts li { display: flex; align-items: center; justify-content: flex-end; gap: 10px; }
  .contacts svg { width: 14px; height: 14px; fill: var(--white); flex: none; }
</style>
</head>
<body>
<main class="sheet">
  <section class="card card-front">
    <div class="front-brand"><span class="dot"></span>Brightly Settled Home Staging</div>
  </section>

  <section class="card card-back">
    <svg class="wave" viewBox="0 0 640 366" preserveAspectRatio="none" aria-hidden="true">
      <path d="M0,190 C170,150 300,265 430,225 C520,195 590,150 640,140 L640,366 L0,366Z" fill="var(--stripe-mid)"/>
      <path d="M0,205 C170,165 300,280 430,240 C520,212 590,168 640,158 L640,366 L0,366Z" fill="var(--stripe-dark)"/>
      <path d="M0,222 C170,185 300,300 430,262 C520,234 590,190 640,182 L640,366 L0,366Z" fill="var(--aqua)"/>
    </svg>

    <div class="brand"><span class="dot"></span>Brightly Settled Home Staging</div>

    <div class="person">
      <p class="person-name">Marisol <span class="surname">Thistlewood</span></p>
      <p class="person-title">Managing Director</p>
    </div>

    <ul class="contacts">
      <li>757-555-0193
        <svg viewBox="0 0 24 24"><path d="M6.6 10.8a15.1 15.1 0 0 0 6.6 6.6l2.2-2.2c.3-.3.7-.4 1-.2 1.1.4 2.3.6 3.6.6.6 0 1 .4 1 1V20c0 .6-.4 1-1 1A17 17 0 0 1 3 4c0-.6.4-1 1-1h3.5c.6 0 1 .4 1 1 0 1.3.2 2.5.6 3.6.1.3 0 .7-.2 1z"/></svg></li>
      <li>www.brightlysettled.com
        <svg viewBox="0 0 24 24"><path d="M12 2a10 10 0 1 0 0 20 10 10 0 0 0 0-20zm6.9 6h-3a15 15 0 0 0-1.3-3.9A8 8 0 0 1 18.9 8zM12 4c.8 1.2 1.5 2.5 1.9 4h-3.8c.4-1.5 1.1-2.8 1.9-4zM4.3 14a8 8 0 0 1 0-4h3.4a16 16 0 0 0 0 4zm.8 2h3a15 15 0 0 0 1.3 3.9A8 8 0 0 1 5.1 16zm3-8h-3a8 8 0 0 1 4.3-3.9A15 15 0 0 0 8.1 8zM12 20c-.8-1.2-1.5-2.5-1.9-4h3.8c-.4 1.5-1.1 2.8-1.9 4zm2.3-6H9.7a14 14 0 0 1 0-4h4.6a14 14 0 0 1 0 4zm.3 5.9a15 15 0 0 0 1.3-3.9h3a8 8 0 0 1-4.3 3.9zm1.7-5.9a16 16 0 0 0 0-4h3.4a8 8 0 0 1 0 4z"/></svg></li>
      <li>marisol@brightlysettled.com
        <svg viewBox="0 0 24 24"><path d="M2 5h20v14H2zm2 2v.5l8 5 8-5V7zm0 2.8V17h16V9.8l-8 5z"/></svg></li>
    </ul>
  </section>
</main>
</body>
</html>
```